Dunfield Inc 1 pg brochure for entrepreneurs

We need a one page brochure (2 sided) designed for a finance and strategy consulting company called Dunfield Inc. which does work in Canada and the United States currently. This company works with entrepreneurs, helping them to establish finance operations, evaluate their financial infomation and apply insight from it to business strategies. Essentially we help entrepreneurs grow their business ... we take care of their finance needs and give them sound business advice ... allowing them to focus on their core business and business strategy.

This one page brochure is meant to caputure what services we provide but also positon that we are also entrepreneurs and we understand how entrepreneurs think .... we not only bring technical competence but cultural insight in this regard as well. We understand how nimble and stealth an entrepreneur's business is so we don't gouge them with expensive consulting fees. We don't want to look like a massive corporation ...we want to look professional, smart and reliable. We want to reflect that we are entrepreneural ourselves even in fact that we have a niche offering that is totally targeted to businesses of this nature.

Major emphasis points for the piece are
1) our core values, this could be a side bar or box
2) the credentials of our founder, he is technically competent and an entrepreneur himself (we have his picture to include)
3) our offerings, what we can do for a company, the client quotes provided are a good illustration of what we offer, the relief we provide a client and of what value we provide - make sure you read these, this could also be a side bar or box, some kind of special call out so the service offerings are very clear

The brochure needs to be editable, so in a format that we can work with it for future, if we need to make updates, one that we can use in Microsoft word and convert to a PDF format. It will be emailed to people (in pdf) and also brought to meetings.

We have a new logo and this design should be an extenstion of it from a colour, look and feel perspective. The piece should also be clean and not too copy heavy so we encourage use of sub-heads, whitespace, etc.

When we send this piece out or hand it to someone, the impression should be "I am comfortable with Dunfield Inc. they can help me and are people who get me, people I can trust to work closely with me on my business who are personally vested in my success".

Hello all, thank you for sumitting designs, there is some great work here.  A few changes/requests ...

Pls add the following headline on the front page right off the top

Entrepreneurs helping entrepreneurs, providing strategic financial services

Can we put Services on the front page? and call them out with treatment in a text box or with something strong that creates emphasis

Can the quote pls be broken up as opposed to one long list of 6 quotes? They can be floated throughout the piece, we can use less of them (or not) and put them on the front and back of the brochure? 

Also looking for the final product to be a little more bold in colour ...

Thx all, let us know if you have questions

Target Market(s)

Individuals (CEO) who runs their own established, yet growing business, who needs a business-minded CFO

Industry/Entity Type

Financial

Requirements
Must have
• Must have photo of founder, include his name and credentials under photo
All copy provide must be included
If not sure of a headline put in dummy text and we will provide headline or sub head copy
Should not have
• Fonts to be clean, no serif fonts. Should compliment logo, not the same font exactly but easily replicable in Microsoft Word and complimentary
No illustrations or cliche clip art

```html
<!DOCTYPE html>
<html lang="en">
<head>
<meta charset="utf-8">
<title>Dunfield Inc – Brochure</title>
<link rel="stylesheet" href="https://fonts.googleapis.com/css2?family=Arimo:ital,wght@0,400;0,700;1,400&family=Roboto:wght@300;700&family=Roboto+Condensed:wght@700&display=swap">
<style>
:root{
  --backdrop:#231f20;
  --paper:#ffffff;
  --navy:#1c1e63;
  --tab:#1f63b3;
  --tab-dark:#123f80;
  --teal:#2cb4da;
  --quote-bg:#e5e6e7;
  --body:#4a4a4a;
  --rule:#333;
}
*{margin:0;padding:0;box-sizing:border-box}
html,body{width:1200px;height:785px;overflow:hidden;background:var(--backdrop)}
body{font-family:"Arimo",Arial,sans-serif;color:var(--body);position:relative}
.page{position:absolute;top:46px;width:536px;height:695px;background:var(--paper)}
.page--front{left:46px}
.page--back{left:617px}
.abs{position:absolute}

/* header */
.brand{left:44px;top:26px;display:flex;align-items:center;gap:8px}
.brand__mark{width:58px;height:56px;background:var(--tab)}
.brand__name{font-size:21px;color:var(--navy);line-height:1}
.brand__tagline{font-size:9px;color:var(--teal);margin-top:3px}
.address{left:285px;top:36px;width:95px;font-size:9.6px;line-height:14.5px;color:#333}
.contact{left:384px;top:36px;font-size:9.6px;line-height:14.5px;color:#333}
.contact b{margin-right:5px}
.header-rule{left:44px;top:92px;width:459px;height:1px;background:var(--rule)}

.headline{left:44px;top:116px;width:300px;font-family:"Roboto",Arial,sans-serif;font-size:37px;font-weight:300;line-height:44px;color:var(--navy)}
.subhead{left:44px;top:257px;font-family:"Roboto",Arial,sans-serif;font-size:15px;font-weight:700;color:var(--navy)}
.intro{left:44px;top:296px;width:262px;font-size:9.6px;line-height:14px}

.tab{position:absolute;height:21px;background:var(--tab);color:#fff;font-size:13.5px;line-height:21px;padding-left:8px}
.tab::before{content:"";position:absolute;right:-1px;top:0;width:14px;height:21px;background:var(--tab-dark);clip-path:polygon(0 0,100% 0,100% 100%)}

.who-tab{left:44px;top:380px;width:118px}
.who-text{left:44px;top:415px;width:290px;font-size:8.5px;line-height:13px}
.founder-photo{left:43px;top:478px;width:112px;height:152px;background:linear-gradient(160deg,#5a4d47,#1d1a1a)}
.founder-bio{left:167px;top:468px;width:150px;font-size:8.5px;line-height:13px}
.founder-bio p+p{margin-top:13px}
.founder-name{left:167px;top:611px;font-size:8.6px;color:#333}
.founder-name small{display:block;font-size:6px;margin-top:2px}

.services{left:340px;top:123px;width:155px;height:347px;background:var(--teal);border-radius:8px}
.services-tab{left:351px;top:115px;width:120px}
.services ul{list-style:none;padding:34px 12px 0 9px}
.services li{position:relative;padding-left:13px;color:#fff;font-size:9.6px;line-height:12.3px;margin-bottom:8px}
.services li svg{position:absolute;left:0;top:2px}

.quote{position:absolute;background:var(--quote-bg);border-radius:8px;font-style:italic;font-size:8.4px;line-height:12.6px;color:#333;padding:0 11px}
.quote--a{left:340px;top:482px;width:155px;height:93px;padding-top:8px}
.quote--b{left:340px;top:588px;width:155px;height:52px;padding-top:7px}

/* back */
.hero{left:44px;top:63px;width:254px;height:152px;background:linear-gradient(120deg,#0d2a4e,#24598c 55%,#0b1d36)}
.bio{left:47px;top:224px;width:258px;font-size:8.6px;line-height:13.2px}
.bio p+p{margin-top:13.2px}

.values{left:324px;top:79px;width:175px;height:391px;background:var(--teal);border-radius:8px}
.values-tab{left:334px;top:69px;width:128px}
.values ul{list-style:none;padding:36px 14px 0 15px}
.values li{position:relative;padding-left:13px;color:#fff;font-size:9.6px;line-height:12.3px;margin-bottom:12px}
.values li::before{content:"";position:absolute;left:0;top:2px;width:7px;height:7px;background:var(--tab)}
.values strong{font-family:"Roboto Condensed",Arial,sans-serif;font-weight:700;letter-spacing:.2px}

.testimonials{left:33px;top:518px;width:465px;height:120px;background:var(--quote-bg);border-radius:8px}
.testimonials-tab{left:43px;top:506px;width:120px}
.tq{position:absolute;font-style:italic;font-size:8.2px;line-height:12.5px;color:#333}
.tq1{left:18px;top:28px;width:126px}
.tq2{left:146px;top:17px;width:142px;padding-left:11px;border-left:1px solid #999;height:92px}
.tq3{left:296px;top:17px;width:160px;padding-left:7px;border-left:1px solid #999;height:36px}
.tq3 span{margin-left:36px}
.tq-rule{left:156px;top:71px;width:296px;height:1px;background:#aaa}
.tq4{left:159px;top:82px;width:295px}
</style>
</head>
<body>

<section class="page page--front">
  <div class="abs brand">
    <div class="brand__mark"></div>
    <div>
      <div class="brand__name">Dunfield Inc</div>
      <div class="brand__tagline">Aligning Finance and Vision</div>
    </div>
  </div>
  <div class="abs address">215 Park Street SW,<br>Calgary Alberta,<br>Canada, T2X 1A4</div>
  <div class="abs contact"><b>P :</b>403.555.0182<br><b>E :</b>martink@dunfieldinc.ca</div>
  <div class="abs header-rule"></div>

  <h1 class="abs headline">Entrepreneurs helping entrepreneurs,</h1>
  <h2 class="abs subhead">providing strategic financial services</h2>
  <p class="abs intro">By engaging Dunfield Inc, entrepreneurs can regularly access senior executive financial acumen and strategic discipline without having to hire a full-time financial executive or overspend on third-party service providers who are transactional in nature.</p>

  <div class="tab who-tab">Who we are?</div>
  <p class="abs who-text">Dunfield Inc. evolved out of the companies, partnerships and relationships that Martin Keller, its founder, has nurtured and built over the last 22 years. Mr. Keller, the founder of Dunfield, is an entrepreneur himself having built his own companies and managed</p>
  <div class="abs founder-photo" role="img" aria-label="Portrait photo of founder Martin Keller"></div>
  <div class="abs founder-bio">
    <p>several successful investment funds whose mandates were to invest in entrepreneurial growth companies.</p>
    <p>Over his career, he has worked extensively with entrepreneurs like himself who have struggled to build an experienced and engaged executive management team.</p>
  </div>
  <div class="abs founder-name">Martin Keller,<small>Founder</small></div>

  <div class="abs services">
    <ul>
      <li><svg width="9" height="8" viewBox="0 0 9 8"><path d="M1 4l2.5 3L8 1" fill="none" stroke="#1f63b3" stroke-width="1.4"/></svg>We work intimately with our clients to determine their corporate and personal objectives</li>
      <li><svg width="9" height="8" viewBox="0 0 9 8"><path d="M1 4l2.5 3L8 1" fill="none" stroke="#1f63b3" stroke-width="1.4"/></svg>We evaluate corporate strategies and assist in aligning them with financial ones</li>
      <li><svg width="9" height="8" viewBox="0 0 9 8"><path d="M1 4l2.5 3L8 1" fill="none" stroke="#1f63b3" stroke-width="1.4"/></svg>We assist in budgeting, investing, financial forecasting and analysis and asset management</li>
      <li><svg width="9" height="8" viewBox="0 0 9 8"><path d="M1 4l2.5 3L8 1" fill="none" stroke="#1f63b3" stroke-width="1.4"/></svg>We develop and implement accountability financial systems, processes and reporting</li>
      <li><svg width="9" height="8" viewBox="0 0 9 8"><path d="M1 4l2.5 3L8 1" fill="none" stroke="#1f63b3" stroke-width="1.4"/></svg>We manage capital raising efforts, tax structuring issues and corporate transactions including mergers, acquisitions, and the sale of your business</li>
    </ul>
  </div>
  <div class="tab services-tab">Services</div>

  <p class="quote quote--a">“I need a financial executive who gets the numbers, can think strategically and translate that combined expertise and understanding into forward-looking corporate strategies” powerful</p>
  <p class="quote quote--b">“I need a financial executive who understands the inherent makeup of an entrepreneur”</p>
</section>

<section class="page page--back">
  <div class="abs hero" role="img" aria-label="Photo of a businessman writing strategy words on a glass board"></div>
  <div class="abs bio">
    <p>Mr. Keller has a proven track record of developing and implementing strategic corporate policy. His experience and education is in corporate finance, portfolio management and building businesses and he is a registered Portfolio Manager. He also has earned an MBA from the Lakeshore University (1995) and is a Chartered Financial Analyst (CFA, 1999).</p>
    <p>He applies this competence to evaluating an entrepreneur's vision and corporate strategies and assisting in translating them into higher growth, improved efficiency and higher profitability. He has extensive experience in public and private, debt and equity capital markets, involving raising, managing and investing capital and completing corporate transactions. He has evaluated hundreds of corporate business strategies for potential investment.</p>
    <p>Other core skills include financial and tax analysis, working with high-performing investment teams, managing financial and accounting functions, designing and implementing operational and compliance systems.</p>
  </div>

  <div class="abs values">
    <ul>
      <li>We love working with entrepreneurs because they like <strong>adventure</strong>. We understand the high energy, creativity and passion required to take high risks and achieve a corporate vision.</li>
      <li>We like entrepreneurs because they are focused on <strong>achievement</strong>. They are “can-do” people who take action.</li>
      <li>We like entrepreneurs because their business relationships are like <strong>family</strong>. Entrepreneurs are personally invested and value personal relationships with amazing people.</li>
      <li>We like entrepreneurs because they work hard and live well. <strong>Health and wellness</strong> is as important as financial success, and most of all having fun is central to the mind set of most successful entrepreneurs.</li>
    </ul>
  </div>
  <div class="tab values-tab">Core Values</div>

  <div class="abs testimonials">
    <p class="tq tq1">“If I could hire a right-hand who I trust intimately to help me with financial matters, I could free up more time to run the business or work on strategy”</p>
    <p class="tq tq2">“I would be a billionaire if I could implement better financial systems and apply strategic discipline.”</p>
    <p class="tq tq3">“If I could hire my equal in a financial capacity, my executive team would be complete”<span>martin's fave</span></p>
    <div class="abs tq-rule"></div>
    <p class="tq tq4">“I need help implementing better financial systems and process that can be maintained in a disciplined way”</p>
  </div>
  <div class="tab testimonials-tab">Testimonials</div>
</section>

</body>
</html>
```